Yard sign design for high end luxury home builder.

Need a design for signage on custom homes that are being built. I already have a logo that I am satisfied with that needs to be incorporated. I need the following incorporated in the design of the sign-
- Lic number 381526
- phone number (805) 555-0148‬
- quennbuilderscrew.com
- Logo/Branding

If possible it may be nice to have the following quote that is on are business cards-

Quote from Gerard of Norvelle-
HE WHO WORKS WITH HIS HANDS IS A LABORER.
HE WHO WORKS WITH HIS HANDS & HIS HEAD IS A CRAFTSMAN.
HE WHO WORKS WITH HIS HANDS & HIS HEAD & HIS HEART IS AN ARTISAN.
-GERARD OF NORVELLE

Target Market(s)

Archetect, Designers, Clients desiring to build a new home or remodel.

Colors
fde9d4
fee4d5
fabb94
fac994
faa54b
f68d4d
f37122
f78f20
f68e4e

Requirements
Must have
• - Lic number 381526
• - phone number (805) 555-0148‬
• - quennbuilderscrew.com
• - Logo/Branding
Nice to have
• Quote from Gerard of Norvelle-
• HE WHO WORKS WITH HIS HANDS IS A LABORER.
• HE WHO WORKS WITH HIS HANDS & HIS HEAD IS A CRAFTSMAN.
• HE WHO WORKS WITH HIS HANDS & HIS HEAD & HIS HEART IS AN ARTISAN.
• -GERARD OF NORVELLE
• OR the below statement-
• Craftsmen that Care
Should not have
• Any additional verbiage not specified above including any type of verbiage about what kind of company we are. For instance- Integrity, reputable... It's just all played out. Im just looking for a bitching design that has the info that compliments my logo/branding.

```html
<!DOCTYPE html>
<html lang="en">
<head>
<meta charset="utf-8">
<title>Quenn Builders Crew – Yard Sign</title>
<link rel="stylesheet" href="https://fonts.googleapis.com/css2?family=Montserrat:ital,wght@0,500;0,600;0,700;0,800;1,500&family=Ubuntu:wght@500&display=swap">
<style>
  :root {
    --page-bg: #e4e4e4;
    --sign-top: #d7d7d7;
    --sign-bottom-start: #ececec;
    --sign-bottom-end: #ffffff;
    --orange-deep: #f37122;
    --orange-light: #f78f20;
    --brand-tan: #8b7c69;
    --ink: #111111;
    --quote-brown: #5a4430;
    --white: #ffffff;
  }
  * { margin: 0; padding: 0; box-sizing: border-box; }
  html, body {
    width: 1200px; height: 1000px; overflow: hidden;
    background: var(--page-bg);
  }
  .sign {
    position: absolute;
    left: 268px; top: 42px;
    width: 664px; height: 886px;
    background: linear-gradient(to bottom, var(--sign-bottom-start), var(--sign-bottom-end));
    display: flex; flex-direction: column;
    font-family: "Montserrat", sans-serif;
  }
  .brand-area {
    height: 410px;
    background: var(--sign-top);
    display: flex; flex-direction: column;
    align-items: center; justify-content: center;
    gap: 22px;
    padding-top: 20px;
  }
  .brand-square {
    width: 150px; height: 150px;
    background: var(--brand-tan);
  }
  .brand-name {
    font-family: "Montserrat", sans-serif;
    font-weight: 800;
    color: var(--brand-tan);
    text-align: center;
    line-height: 1;
  }
  .brand-name .main { display: block; font-size: 50px; letter-spacing: 3px; }
  .brand-name .sub { display: block; font-size: 19px; letter-spacing: 1.5px; margin-top: 6px; }
  .sale-band {
    height: 146px;
    background: linear-gradient(to bottom, var(--orange-deep), var(--orange-light));
    display: flex; align-items: center; justify-content: center;
  }
  .sale-band h1 {
    color: var(--white);
    font-weight: 800;
    font-size: 112px;
    letter-spacing: -1px;
    line-height: 1;
  }
  .contact {
    text-align: center;
    color: var(--ink);
    padding-top: 14px;
  }
  .contact .phone { font-size: 72px; font-weight: 700; line-height: 1.1; letter-spacing: 0.5px; }
  .contact .web { font-size: 31px; font-weight: 600; margin-top: 8px; }
  .contact .license { font-size: 21px; font-weight: 500; margin-top: 14px; }
  .quote {
    margin-top: auto;
    padding: 0 30px 24px;
    font-family: "Ubuntu", sans-serif;
    font-weight: 500;
    color: var(--quote-brown);
    text-align: center;
    font-size: 15px;
    line-height: 1.32;
  }
  .quote cite {
    display: block;
    text-align: right;
    font-style: italic;
    font-family: "Montserrat", sans-serif;
    padding-right: 0;
    margin-top: 4px;
  }
</style>
</head>
<body>
  <main class="sign">
    <section class="brand-area">
      <div class="brand-square" aria-hidden="true"></div>
      <div class="brand-name">
        <span class="main">QUENN</span>
        <span class="sub">BUILDERS CREW INC.</span>
      </div>
    </section>
    <section class="sale-band">
      <h1>FOR SALE</h1>
    </section>
    <section class="contact">
      <p class="phone">(805) 555-0148</p>
      <p class="web">www.quennbuilderscrew.com</p>
      <p class="license">LIC NUMBER 381526</p>
    </section>
    <blockquote class="quote">
      <p>HE WHO WORKS WITH HIS HANDS IS A LABORER.</p>
      <p>HE WHO WORKS WITH HIS HANDS &amp; HIS HEAD IS A CRAFTSMAN.</p>
      <p>HE WHO WORKS WITH HIS HANDS &amp; HIS HEAD &amp; HIS HEART IS AN ARTISAN.</p>
      <cite>–GERARD OF NORVELLE</cite>
    </blockquote>
  </main>
</body>
</html>
```